Dermatologist office in Brasilia. My with "target customers" are specially women.

I’m a dermatologist who works since 2006 in Brasilia. In 2017 I decided to change and improve my career. I decided to work more with cosmetics (Lumiqa and fillers), I still work with clinical and surgical dermatology.
Most of my patients are women but 20-30% are children and men.
I would like to see designs that use a butterfly and the color aquamarine with details in gold.

Industry/Entity Type

Cosmetics

Font styles to use
Sans Serif

Colors
33b8a4
87cfc6
cfeae6
85cae6

Requirements
Must have
• My project must have my name (Harumi Okeda) and my medical specialty (Dermatologista)
Nice to have
• The colors I prefer are aquamarine or Corvell Jade Tin.
• I also prefer a butterfly that means transformation and a new life.
• I prefer a sofisticated and also minimalist design.

```html
<!DOCTYPE html>
<html lang="en">
<head>
<meta charset="utf-8">
<title>Harumi Okeda – Business Card</title>
<link rel="stylesheet" href="https://fonts.googleapis.com/css2?family=Josefin+Sans:wght@400;600&family=Raleway:wght@400;600&display=swap">
<style>
  :root {
    --teal: #33b8a4;
    --aqua: #87cfc6;
    --mist: #cfeae6;
    --sky: #85cae6;
    --ink: #2b2b2b;
    --grey: #5e5e5e;
    --rule: #bdbdbd;
    --paper: #ffffff;
    --backdrop: #ecefee;
  }
  * { margin: 0; padding: 0; box-sizing: border-box; }
  html, body { width: 1200px; height: 900px; overflow: hidden; }
  body {
    background: var(--backdrop);
    position: relative;
    font-family: "Raleway", sans-serif;
  }
  .card {
    position: absolute;
    left: 250px;
    width: 700px;
    height: 400px;
    background: var(--paper);
    border-radius: 22px;
    overflow: hidden;
    box-shadow: 0 6px 18px rgba(0,0,0,0.12);
  }
  .card--front { top: 30px; }
  .card--back { top: 470px; }

  .brand {
    position: absolute;
    display: flex;
    flex-direction: column;
    align-items: center;
    font-family: "Josefin Sans", sans-serif;
    color: var(--ink);
  }
  .brand__mark {
    width: 70px;
    height: 70px;
    border-radius: 50%;
    background: var(--teal);
    margin-bottom: 30px;
  }
  .brand__name {
    font-size: 26px;
    font-weight: 400;
    letter-spacing: 0.5em;
    margin-right: -0.5em;
    white-space: nowrap;
  }
  .brand__role {
    font-size: 10px;
    letter-spacing: 0.55em;
    margin-right: -0.55em;
    margin-top: 8px;
  }
  .card--front .brand { left: 0; right: 0; top: 110px; }
  .card--back .brand { left: 40px; width: 330px; top: 95px; }

  .divider {
    position: absolute;
    left: 400px;
    top: 45px;
    width: 1px;
    height: 205px;
    background: var(--rule);
  }
  .contact {
    position: absolute;
    left: 430px;
    top: 42px;
    color: var(--grey);
    z-index: 1;
  }
  .contact__name {
    font-size: 25px;
    font-weight: 600;
    line-height: 1.2;
    color: var(--ink);
    opacity: 0.8;
    letter-spacing: 0.01em;
  }
  .contact__role {
    font-size: 14px;
    line-height: 1.3;
    color: var(--teal);
    margin-bottom: 10px;
  }
  .contact__address {
    font-size: 13px;
    line-height: 1.4;
    font-style: normal;
    margin-bottom: 10px;
  }
  .contact__list { list-style: none; font-size: 13px; line-height: 1.45; }
  .contact__list li { display: flex; align-items: center; gap: 8px; }
  .contact__list svg { width: 10px; height: 10px; flex: none; }

  .wave { position: absolute; left: 0; bottom: 0; width: 700px; height: 400px; }
</style>
</head>
<body>

<section class="card card--front" aria-label="Card front">
  <div class="brand">
    <span class="brand__mark"></span>
    <span class="brand__name">HARUMI OKEDA</span>
    <span class="brand__role">DERMATOLOGIST</span>
  </div>
</section>

<section class="card card--back" aria-label="Card back">
  <svg class="wave" viewBox="0 0 700 400" aria-hidden="true">
    <path d="M0 384 C260 380 420 300 530 262 C600 240 650 234 700 232 L700 400 L0 400 Z" fill="var(--sky)"/>
    <path d="M0 388 C262 384 423 305 533 267 C603 245 652 239 700 237" fill="none" stroke="var(--paper)" stroke-width="2"/>
    <path d="M0 391 C264 387 425 309 535 271 C605 249 654 243 700 241 L700 400 L0 400 Z" fill="var(--teal)"/>
  </svg>

  <div class="brand">
    <span class="brand__mark"></span>
    <span class="brand__name">HARUMI OKEDA</span>
    <span class="brand__role">DERMATOLOGIST</span>
  </div>

  <div class="divider"></div>

  <div class="contact">
    <h1 class="contact__name">HARUMI OKEDA</h1>
    <p class="contact__role">Dermatologist</p>
    <address class="contact__address">418/B Elm Row,<br>Midtown, Riverton, USA</address>
    <ul class="contact__list">
      <li>
        <svg viewBox="0 0 10 10" aria-hidden="true"><path d="M2 1 L4 1 L4.6 3 L3.5 4 Q4.5 6 6 6.5 L7 5.4 L9 6 L9 8 Q5 9 2 6 Q1 4 2 1 Z" fill="var(--teal)"/></svg>
        0492 615 870
      </li>
      <li>
        <svg viewBox="0 0 10 10" aria-hidden="true"><rect x="1" y="2" width="8" height="6" fill="none" stroke="var(--teal)" stroke-width="1.2"/><path d="M1 2 L5 5.5 L9 2" fill="none" stroke="var(--teal)" stroke-width="1.2"/></svg>
        info@harumiokeda.com.au
      </li>
      <li>
        <svg viewBox="0 0 10 10" aria-hidden="true"><circle cx="5" cy="5" r="4" fill="none" stroke="var(--teal)" stroke-width="1.1"/><path d="M1 5 H9 M5 1 Q2.5 5 5 9 M5 1 Q7.5 5 5 9" fill="none" stroke="var(--teal)" stroke-width="0.9"/></svg>
        www.harumiokeda.com.au
      </li>
    </ul>
  </div>
</section>

</body>
</html>
```